BildeVOLD buisnesscard

Hey :) I need a modern buisnesscard for my company BildeVOLD
It most have:
Dagligleder og Fotograf: Henrik Audun Strandvik

Mob: +4791264085
Epost: post@bildevold.example
Adresse: Kvernbakken9, 6040 Langevåg

Facbook and instagram logo with text BildeVOLD

BildeVOLD logo

It Company

```html
<!DOCTYPE html>
<html lang="no">
<head>
<meta charset="utf-8">
<title>BildeVOLD – visittkort</title>
<link rel="stylesheet" href="https://fonts.googleapis.com/css2?family=Questrial&display=swap">
<style>
  :root {
    --backdrop: #dcd8d2;
    --card: #eef0f1;
    --card-edge: #d4d8dc;
    --navy: #24477a;
    --magenta: #b3275e;
    --band-top: #34618d;
    --band-bottom: #1d3150;
    --muted-text: #c6ccd4;
  }
  * { margin: 0; padding: 0; box-sizing: border-box; }
  html, body {
    width: 1200px;
    height: 969px;
    overflow: hidden;
    background: var(--backdrop);
    font-family: "Questrial", "Century Gothic", sans-serif;
  }
  .business-card {
    position: absolute;
    left: 395px;
    top: 123px;
    width: 410px;
    height: 723px;
    background: var(--card);
    border: 1px solid var(--card-edge);
    overflow: hidden;
  }
  .card-shapes {
    position: absolute;
    inset: 0;
  }
  .brand {
    position: absolute;
    top: 128px;
    left: 0;
    width: 100%;
    display: flex;
    align-items: center;
    justify-content: center;
    gap: 12px;
  }
  .brand-mark {
    width: 26px;
    height: 26px;
    background: var(--navy);
  }
  .brand-name {
    font-size: 44px;
    color: var(--navy);
    letter-spacing: 0.5px;
    line-height: 1;
  }
  .holder-name {
    position: absolute;
    top: 208px;
    width: 100%;
    text-align: center;
    font-size: 26px;
    color: var(--navy);
    letter-spacing: 0.5px;
  }
  .holder-role {
    position: absolute;
    top: 242px;
    width: 100%;
    text-align: center;
    font-size: 20px;
    color: var(--magenta);
  }
  .social {
    position: absolute;
    left: 38px;
    top: 493px;
    display: flex;
    align-items: center;
    gap: 8px;
  }
  .social-dot {
    width: 28px;
    height: 28px;
    border-radius: 50%;
    background: var(--magenta);
  }
  .social-name {
    font-size: 17px;
    color: var(--muted-text);
  }
  .address {
    position: absolute;
    left: 38px;
    top: 538px;
    font-size: 19px;
    line-height: 27px;
    color: var(--muted-text);
  }
  .contact-list {
    position: absolute;
    left: 38px;
    top: 605px;
    list-style: none;
    font-size: 18px;
    line-height: 27px;
    color: var(--muted-text);
  }
  .contact-list li {
    display: flex;
    align-items: center;
    gap: 10px;
  }
  .contact-icon {
    width: 18px;
    height: 18px;
    flex: none;
  }
</style>
</head>
<body>
  <article class="business-card">
    <svg class="card-shapes" width="410" height="723" viewBox="0 0 410 723" aria-hidden="true">
      <defs>
        <linearGradient id="band-fill" x1="0" y1="0" x2="0.4" y2="1">
          <stop offset="0" stop-color="var(--band-top)"/>
          <stop offset="1" stop-color="var(--band-bottom)"/>
        </linearGradient>
      </defs>
      <polygon class="accent-stripe" points="0,258 0,272 410,719 410,705" fill="var(--magenta)"/>
      <polygon class="contact-band" points="0,292 0,723 395,723" fill="url(#band-fill)"/>
    </svg>

    <header class="brand">
      <span class="brand-mark"></span>
      <span class="brand-name">BildeVOLD</span>
    </header>
    <h1 class="holder-name">Henrik Audun Strandvik</h1>
    <p class="holder-role">Dagligleder og Fotograf</p>

    <div class="social">
      <span class="social-dot"></span>
      <span class="social-name">BildeVOLD</span>
    </div>

    <address class="address">
      Kvernbakken9<br>
      6040 Langevåg
    </address>

    <ul class="contact-list">
      <li>
        <svg class="contact-icon" viewBox="0 0 18 18" aria-hidden="true">
          <rect x="5" y="1.5" width="8" height="15" rx="1.5" fill="none" stroke="var(--muted-text)" stroke-width="1.5"/>
          <circle cx="9" cy="13.5" r="1" fill="var(--muted-text)"/>
        </svg>
        <span>+4791264085</span>
      </li>
      <li>
        <svg class="contact-icon" viewBox="0 0 18 18" aria-hidden="true">
          <rect x="2" y="4" width="14" height="10" fill="var(--muted-text)"/>
          <polyline points="2,4 9,10 16,4" fill="none" stroke="var(--band-bottom)" stroke-width="1.3"/>
        </svg>
        <span>post@bildevold.example</span>
      </li>
      <li>
        <svg class="contact-icon" viewBox="0 0 18 18" aria-hidden="true">
          <circle cx="9" cy="9" r="7" fill="none" stroke="var(--muted-text)" stroke-width="1.5"/>
          <ellipse cx="9" cy="9" rx="3" ry="7" fill="none" stroke="var(--muted-text)" stroke-width="1.2"/>
          <line x1="2" y1="9" x2="16" y2="9" stroke="var(--muted-text)" stroke-width="1.2"/>
        </svg>
        <span>www.bildevold.example</span>
      </li>
    </ul>
  </article>
</body>
</html>
```